Webdesign für Hunde- und Katzenernährungsberatung
Zielgruppe
Hunde und Katzenernährungsberatung, für Menschen, die auch bei ihren Hunden und Katzen auf gesunde, natürliche Ernährung achten wollen, ohne unnötigen Geschmacksverstärker, Zucker, Zusatzstoffe, etc. die gesundheitliche Probleme bei den Tieren verursachen können.
Umstellung auf natürliche, artgerechte Fütterung, teils roh, teils gekocht, angepasst auf Grösse, Rasse, Alter etc., auch speziell für Welpen
Beratung bei:
Übergewicht
Allergien
Unverträglichkeiten
Magen-Darm Problemen
individuelle Ernährungspläne
Selbsthergestellte Kekse, Leckerlies, Snacks, Pralinen und div. Hausmannskost in Einmachgläsern (alles auf Vorbestellung).
Diverse Accessoires
Halsbänder, Leinen, Geschirr aus div. natürlichen Materialien
Lern- und Spielzeug aus Holz und Stoff
div. Zubehör für Tiere, sowie auch für Frauchen und Herrchen
Aufgabenstellung
Die Seite sollte stilvoll aber nicht überfüllt sein und im Retro/Vintage Stil gehalten werden, da das Logo bereits sehr wirksam und eher auffällig ist, dezente Töne im Hintergrund, die Nahrungsmittel werden dann ev. auf Schieferplatten oder unauffälligem Hintergrund platziert. Ich sollte zu einem späteren Zeitpunkt selber Fotos, Links, Texte, etc. einfach dazu fügen können.

```html
<!DOCTYPE html>
<html lang="de">
<head>
<meta charset="utf-8">
<title>Pfotenküche – Ernährungsberatung für Hund und Katze</title>
<link rel="stylesheet" href="https://fonts.googleapis.com/css2?family=Kaushan+Script&family=Montserrat:wght@400;600;700&family=Open+Sans:wght@400;600&display=swap">
<style>
:root{
  --backdrop:#e6e6e6;
  --page:#f7f7f7;
  --white:#ffffff;
  --sky:#9cc6e0;
  --sky-light:#b9d8ec;
  --steel:#6f9ab8;
  --steel-dark:#5f88a6;
  --orange:#c8782a;
  --orange-light:#f2c58a;
  --brown:#7a4a1c;
  --logo-blue:#7fb7d9;
  --text:#555555;
  --text-soft:#8a8a8a;
  --line:#d6d6d6;
}
*{margin:0;padding:0;box-sizing:border-box}
html,body{width:1200px;height:3000px;overflow:hidden}
body{background:radial-gradient(ellipse at center,#f4f4f4 0%,var(--backdrop) 70%);font-family:"Montserrat",sans-serif;color:var(--text)}
.page{position:absolute;left:396px;top:0;width:408px;height:3000px;background:var(--page);overflow:hidden}
.abs{position:absolute}
.script{font-family:"Kaushan Script",cursive;font-weight:400}
.btn{position:absolute;display:flex;align-items:center;justify-content:center;font-size:6.5px;font-weight:700;color:var(--white);text-transform:uppercase;letter-spacing:.2px}
.btn--steel{background:var(--steel)}
.btn--orange{background:var(--orange)}
.photo{position:absolute}
.body-copy{font-size:6.4px;line-height:11px;color:var(--text)}

/* header */
.header{position:absolute;left:0;top:0;width:408px;height:489px;background:var(--white);border-top:3px solid var(--sky)}
.header__badge{position:absolute;left:24px;top:10px;display:flex;align-items:center;gap:5px}
.header__badge-dot{width:14px;height:14px;border-radius:50%;background:var(--logo-blue)}
.header__badge-name{font-size:10px;font-weight:700;color:var(--logo-blue)}
.header__menu{position:absolute;left:366px;top:22px;width:24px}
.header__menu span{display:block;height:1.5px;background:var(--sky);margin-bottom:2.5px}
.brand{position:absolute;left:150px;top:62px;width:240px;text-align:center}
.brand__name{font-size:30px;font-weight:700;color:var(--logo-blue);letter-spacing:1px}
.brand__circle{width:190px;height:190px;border-radius:50%;background:#e4f0f8;margin:14px auto 0}
.hero__arrow{left:78px;top:198px;width:72px;height:146px;background:linear-gradient(180deg,#fbf1e4,#f6e2c8);border-radius:30px}
.hero__rule{position:absolute;left:100px;width:206px;height:2px;background:var(--brown);border-radius:1px}
.hero__title{position:absolute;left:0;top:362px;width:408px;text-align:center;font-size:31px;color:var(--brown)}
.hero__title .accent{color:var(--orange)}
.hero__sub{position:absolute;left:0;top:405px;width:408px;text-align:center;font-size:8.4px;color:var(--brown)}
.hero__border{position:absolute;left:0;top:486px;width:408px;height:3px;background:var(--orange-light)}

/* welcome */
.heading{position:absolute;color:var(--orange);line-height:1.15}
.list-caps{font-size:8px;line-height:13px;color:#444;text-transform:uppercase}
.list-caps .sep{color:var(--orange)}

/* blue bands */
.band{position:absolute;left:0;width:408px;background:radial-gradient(circle at 45% 50%,var(--sky-light),var(--sky) 65%)}
.wave{position:absolute;left:0;width:408px;height:8px}
.ticklist{list-style:none;font-size:5.6px;font-weight:700;color:var(--white);text-transform:uppercase;line-height:13.5px}
.ticklist li{display:flex;align-items:center;gap:5px}
.zub-list{list-style:none;font-size:5.6px;font-weight:700;color:var(--orange);text-transform:uppercase;line-height:11px}

/* shop */
.shop__title{position:absolute;left:0;top:1852px;width:408px;text-align:center;font-size:22px;color:var(--white)}
.shop__nav{position:absolute;left:0;top:1890px;width:408px;text-align:center;font-size:5.6px;font-weight:700;color:var(--white);word-spacing:2px}
.card{position:absolute;width:117px;height:195px;background:var(--white);box-shadow:0 1px 4px rgba(0,0,0,.12);text-align:center}
.card__img{position:absolute;left:12px;top:8px;width:93px;height:60px;border-radius:40%;background:radial-gradient(ellipse,#a0542a,#c77a44 55%,#fff 72%)}
.card__name{position:absolute;left:0;top:79px;width:117px;font-size:5.6px;font-weight:700;color:var(--orange)}
.card__dots{position:absolute;left:10px;top:89px;width:97px;border-top:1px dotted #ccc}
.card__desc{position:absolute;left:8px;top:94px;width:101px;font-size:4.8px;line-height:7.5px;color:var(--text)}
.card__rule{position:absolute;left:10px;top:128px;width:97px;border-top:1px dotted #ccc}
.card__price{position:absolute;left:0;top:133px;width:117px;font-size:20px;font-weight:600;color:var(--orange)}
.card__note{position:absolute;left:0;top:157px;width:117px;font-size:4.4px;line-height:6px;color:var(--text)}
.card__note b{color:var(--orange);font-weight:600}
.card .btn{left:14px;top:176px;width:89px;height:13px;font-size:6px}

/* newsletter */
.newsletter{position:absolute;left:0;top:2400px;width:408px;height:95px;background:var(--steel);font-family:"Open Sans",sans-serif;color:var(--white);text-align:center}
.newsletter__title{padding-top:18px;font-size:14.5px;font-weight:400}
.newsletter__sub{font-size:8px;opacity:.9}
.newsletter__input{position:absolute;left:15px;top:54px;width:279px;height:20px;background:var(--white);font-size:7px;color:#aaa;text-align:left;padding:6px 12px}
.newsletter__btn{position:absolute;left:300px;top:54px;width:93px;height:20px;border:1px solid var(--white);background:var(--white);color:var(--steel);font-size:7.5px;font-weight:600;display:flex;align-items:center;justify-content:center}

/* footer */
.footer-brand{position:absolute;left:0;top:2516px;width:408px;text-align:center}
.footer-brand__name{font-size:22px;font-weight:700;color:var(--logo-blue)}
.footer-brand__circle{width:84px;height:84px;border-radius:50%;background:#e4f0f8;margin:6px auto 0}
.address{position:absolute;left:0;width:408px;text-align:center;font-size:6px;color:var(--text)}
.address a{color:var(--orange);text-decoration:none}
.socials{position:absolute;left:0;top:2693px;width:408px;display:flex;justify-content:center;gap:18px}
.socials span{width:14px;height:14px;border-radius:50%;background:#9aa3ab}
.contact__title{position:absolute;left:0;top:2726px;width:408px;text-align:center;font-size:24px;color:var(--orange)}
.contact__sub{position:absolute;left:0;top:2764px;width:408px;text-align:center;font-size:6px;color:var(--text)}
.field{position:absolute;font-size:5.6px;text-transform:uppercase;color:var(--text-soft);border-bottom:1px solid var(--line);padding-bottom:6px}
.field--active{color:var(--orange);border-color:var(--orange-light)}
.copy-check{position:absolute;left:15px;top:2930px;font-size:6px;color:var(--text);display:flex;align-items:center;gap:6px}
.copy-check i{display:block;width:6px;height:6px;background:#bbb}
.bottom-bar{position:absolute;left:0;top:2968px;width:408px;height:32px;background:var(--steel);color:var(--white);font-size:5.6px;display:flex;align-items:center;justify-content:space-between;padding:0 15px}
.bottom-bar nav{font-weight:600;word-spacing:2px}
</style>
</head>
<body>
<main class="page">

  <header class="header">
    <div class="header__badge"><span class="header__badge-dot"></span><span class="header__badge-name">Pfotenküche</span></div>
    <div class="header__menu"><span></span><span></span><span></span></div>
    <div class="brand">
      <div class="brand__name">Pfotenküche</div>
      <div class="brand__circle"></div>
    </div>
    <div class="photo hero__arrow" role="img" aria-label="Handgezeichneter geschwungener Pfeil in Orange"></div>
    <div class="hero__rule" style="top:352px"></div>
    <h1 class="hero__title script">Lorem ipsum <span class="accent">dolor sit amet</span></h1>
    <p class="hero__sub">LOREM IPSUM DOLOR SIT AMET CONSECTETUR ADIPISCING ELIT</p>
    <div class="hero__rule" style="top:424px"></div>
    <a class="btn btn--steel" style="left:150px;top:443px;width:104px;height:20px;font-size:7px">Online Shop</a>
    <div class="hero__border"></div>
  </header>

  <section class="welcome">
    <div class="photo" style="left:0;top:503px;width:192px;height:308px;background:linear-gradient(160deg,#d9cbbd,#8a8f9a 60%,#5c626d);border-radius:0 0 40% 0" role="img" aria-label="Porträt der Ernährungsberaterin im grauen Blazer"></div>
    <h2 class="heading script" style="left:210px;top:524px;font-size:21px">Willkommen auf<br>unserer Website</h2>
    <p class="abs body-copy" style="left:210px;top:583px;width:186px">Lorem ipsum dolor sit amet, consectetur adipiscing elit, sed do eiusmod tempor incididunt ut labore et dolore magna aliqua. Ut enim ad minim veniam, quis nostrud exercitation ullamco laboris nisi ut aliquip ex ea commodo consequat. Duis aute irure dolor in reprehenderit in voluptate velit esse cillum dolore eu fugiat nulla pariatur.</p>
    <h3 class="heading script" style="left:210px;top:655px;font-size:17px">Beratung bei:</h3>
    <p class="abs list-caps" style="left:210px;top:681px">Übergewicht <span class="sep">|</span> Allergien<br>Unverträglichkeiten<br>Magen-Darm Problemen<br>Individuelle Ernährungspläne</p>
    <p class="abs body-copy" style="left:210px;top:738px;width:186px">Lorem ipsum dolor sit amet, consectetur adipiscing elit, sed do eiusmod tempor incididunt ut labore et dolore magna aliqua. Ut enim ad minim veniam, quis nostrud exercitation ullamco laboris nisi ut aliquip ex ea commodo consequat.</p>
  </section>

  <section class="nutrition">
    <h2 class="heading script" style="left:15px;top:833px;font-size:22px">Ernährungsberatung</h2>
    <p class="abs body-copy" style="left:15px;top:871px;width:272px">Lorem ipsum dolor sit amet, consectetur adipiscing elit, sed do eiusmod tempor incididunt ut labore et dolore magna aliqua. Ut enim ad minim veniam, quis nostrud exercitation ullamco laboris nisi ut aliquip ex ea commodo consequat. Duis aute irure dolor in reprehenderit in voluptate velit esse cillum dolore eu fugiat nulla pariatur.</p>
    <p class="abs body-copy" style="left:15px;top:926px;width:180px">Lorem ipsum dolor sit amet, consectetur adipiscing elit, sed do eiusmod tempor incididunt ut labore et dolore magna aliqua.</p>
    <a class="btn btn--orange" style="left:15px;top:963px;width:84px;height:17px">Mehr Infos</a>
    <div class="photo" style="left:205px;top:922px;width:203px;height:214px;background:linear-gradient(200deg,#8a4a22,#c98a52 45%,#f2efec 85%);border-radius:70% 0 0 0" role="img" aria-label="Beagle frisst aus einem Metallnapf"></div>
    <div class="photo" style="left:0;top:1008px;width:200px;height:128px;background:linear-gradient(90deg,#c9b29a,#a8a8ac 70%,#dcdcdc);border-radius:0 50% 0 0" role="img" aria-label="Katze frisst aus einem Metallnapf"></div>
  </section>

  <section class="homemade">
    <div class="band" style="top:1180px;height:292px"></div>
    <svg class="wave" style="top:1174px" viewBox="0 0 408 8" preserveAspectRatio="none" aria-hidden="true"><path d="M0 8 Q4 0 8 8 T16 8 T24 8 T32 8 T40 8 T48 8 T56 8 T64 8 T72 8 T80 8 T88 8 T96 8 T104 8 T112 8 T120 8 T128 8 T136 8 T144 8 T152 8 T160 8 T168 8 T176 8 T184 8 T192 8 T200 8 T208 8 T216 8 T224 8 T232 8 T240 8 T248 8 T256 8 T264 8 T272 8 T280 8 T288 8 T296 8 T304 8 T312 8 T320 8 T328 8 T336 8 T344 8 T352 8 T360 8 T368 8 T376 8 T384 8 T392 8 T400 8 T408 8Z" fill="#a9cfe6"/></svg>
    <svg class="wave" style="top:1470px" viewBox="0 0 408 8" preserveAspectRatio="none" aria-hidden="true"><path d="M0 0 Q4 8 8 0 T16 0 T24 0 T32 0 T40 0 T48 0 T56 0 T64 0 T72 0 T80 0 T88 0 T96 0 T104 0 T112 0 T120 0 T128 0 T136 0 T144 0 T152 0 T160 0 T168 0 T176 0 T184 0 T192 0 T200 0 T208 0 T216 0 T224 0 T232 0 T240 0 T248 0 T256 0 T264 0 T272 0 T280 0 T288 0 T296 0 T304 0 T312 0 T320 0 T328 0 T336 0 T344 0 T352 0 T360 0 T368 0 T376 0 T384 0 T392 0 T400 0 T408 0Z" fill="#a9cfe6"/></svg>
    <div class="photo" style="left:0;top:1180px;width:205px;height:292px;background:linear-gradient(180deg,#d9a867,#e8d5bd 45%,#9ea4aa 70%,#f1ede8);border-radius:0 0 30% 0" role="img" aria-label="Chihuahua hält einen Metallnapf im Maul"></div>
    <div class="photo" style="left:72px;top:1470px;width:184px;height:50px;background:radial-gradient(ellipse,#b0824e,#c99a62 60%,rgba(201,154,98,0) 75%)" role="img" aria-label="Selbstgebackene Hundekekse"></div>
    <h2 class="abs script" style="left:212px;top:1194px;font-size:18px;line-height:21px;color:var(--white)">Hausgemachte<br>Tiernahrung</h2>
    <p class="abs body-copy" style="left:212px;top:1249px;width:186px;color:var(--white)">Lorem ipsum dolor sit amet, consectetur adipiscing elit, sed do eiusmod tempor incididunt ut labore et dolore magna aliqua. Ut enim ad minim veniam, quis nostrud exercitation ullamco laboris nisi ut aliquip ex ea commodo consequat. Duis aute irure dolor in reprehenderit in voluptate velit esse cillum dolore eu fugiat nulla pariatur.</p>
    <h3 class="abs script" style="left:212px;top:1322px;font-size:13px;line-height:14px;color:var(--white)">Sie können in unserem<br>Online-Shop</h3>
    <ul class="abs ticklist" style="left:212px;top:1355px">
      <li><svg width="8" height="6" viewBox="0 0 8 6" aria-hidden="true"><path d="M1 3l2 2 4-4" stroke="#fff" stroke-width="1.2" fill="none"/></svg>Selbsthergestellte Kekse</li>
      <li><svg width="8" height="6" viewBox="0 0 8 6" aria-hidden="true"><path d="M1 3l2 2 4-4" stroke="#fff" stroke-width="1.2" fill="none"/></svg>Leckerlies</li>
      <li><svg width="8" height="6" viewBox="0 0 8 6" aria-hidden="true"><path d="M1 3l2 2 4-4" stroke="#fff" stroke-width="1.2" fill="none"/></svg>Snacks</li>
      <li><svg width="8" height="6" viewBox="0 0 8 6" aria-hidden="true"><path d="M1 3l2 2 4-4" stroke="#fff" stroke-width="1.2" fill="none"/></svg>Pralinen</li>
      <li><svg width="8" height="6" viewBox="0 0 8 6" aria-hidden="true"><path d="M1 3l2 2 4-4" stroke="#fff" stroke-width="1.2" fill="none"/></svg>Div. Hausmannskost in Einmachgläsern</li>
    </ul>
    <a class="btn btn--steel" style="left:212px;top:1432px;width:84px;height:16px">Mehr Infos</a>
  </section>

  <section class="accessories">
    <h2 class="heading script" style="left:15px;top:1540px;font-size:20px">Zubehör</h2>
    <p class="abs body-copy" style="left:15px;top:1577px;width:186px">Lorem ipsum dolor sit amet, consectetur adipiscing elit, sed do eiusmod tempor incididunt ut labore et dolore magna aliqua. Ut enim ad minim veniam, quis nostrud exercitation ullamco laboris nisi ut aliquip ex ea commodo consequat. Duis aute irure dolor in reprehenderit in voluptate velit esse cillum dolore eu fugiat nulla pariatur.</p>
    <p class="abs body-copy" style="left:15px;top:1657px;width:186px">Lorem ipsum dolor sit amet, consectetur adipiscing elit, sed do eiusmod tempor incididunt ut labore et dolore magna aliqua.</p>
    <ul class="abs zub-list" style="left:15px;top:1696px">
      <li>Halsbänder</li><li>Leinen</li><li>Geschirr aus div. natürlichen Materialien</li><li>Lern- und Spielzeug aus Holz und Stoff</li><li>Div. Zubehör für Tiere</li>
    </ul>
    <a class="btn btn--steel" style="left:15px;top:1760px;width:84px;height:16px">Mehr Infos</a>
    <div class="photo" style="left:206px;top:1509px;width:202px;height:303px;background:linear-gradient(200deg,#c99560,#d8b48a 35%,#8d8680 65%,#f3f1ee);border-radius:50% 0 0 10%" role="img" aria-label="Kätzchen vor einem Holz-Spielzeug mit Leckerlies"></div>
  </section>

  <section class="shop">
    <div class="band" style="top:1841px;height:559px"></div>
    <svg class="wave" style="top:1835px" viewBox="0 0 408 8" preserveAspectRatio="none" aria-hidden="true"><path d="M0 8 Q4 0 8 8 T16 8 T24 8 T32 8 T40 8 T48 8 T56 8 T64 8 T72 8 T80 8 T88 8 T96 8 T104 8 T112 8 T120 8 T128 8 T136 8 T144 8 T152 8 T160 8 T168 8 T176 8 T184 8 T192 8 T200 8 T208 8 T216 8 T224 8 T232 8 T240 8 T248 8 T256 8 T264 8 T272 8 T280 8 T288 8 T296 8 T304 8 T312 8 T320 8 T328 8 T336 8 T344 8 T352 8 T360 8 T368 8 T376 8 T384 8 T392 8 T400 8 T408 8Z" fill="#a9cfe6"/></svg>
    <h2 class="shop__title script">Online Shop</h2>
    <p class="shop__nav">ALLE PRODUKTE &nbsp;|&nbsp; FOOD &nbsp;|&nbsp; SNACKS &nbsp;|&nbsp; PRALINEN &nbsp;|&nbsp; ZUBEHÖR</p>

    <article class="card" style="left:15px;top:1916px"><div class="card__img" role="img" aria-label="Trockenfutter-Stücke"></div><h3 class="card__name">PRODUKTNAME GEHT HIER</h3><div class="card__dots"></div><p class="card__desc">Lorem ipsum dolor sit amet, consectetur adipiscing elit, sed do eiusmod tempor incididunt ut labore et dolore magna aliqua.</p><div class="card__rule"></div><p class="card__price">€ 10,50</p><p class="card__note">inkl. 19% MwSt. zzgl.<br><b>Versandkosten</b> &nbsp;|&nbsp; Lieferzeit 2 - 3 tage</p><a class="btn btn--orange">In den Warenkorb</a></article>
    <article class="card" style="left:146px;top:1916px"><div class="card__img" role="img" aria-label="Trockenfutter-Stücke"></div><h3 class="card__name">PRODUKTNAME GEHT HIER</h3><div class="card__dots"></div><p class="card__desc">Lorem ipsum dolor sit amet, consectetur adipiscing elit, sed do eiusmod tempor incididunt ut labore et dolore magna aliqua.</p><div class="card__rule"></div><p class="card__price">€ 10,50</p><p class="card__note">inkl. 19% MwSt. zzgl.<br><b>Versandkosten</b> &nbsp;|&nbsp; Lieferzeit 2 - 3 tage</p><a class="btn btn--steel">In den Warenkorb</a></article>
    <article class="card" style="left:276px;top:1916px"><div class="card__img" role="img" aria-label="Trockenfutter-Stücke"></div><h3 class="card__name">PRODUKTNAME GEHT HIER</h3><div class="card__dots"></div><p class="card__desc">Lorem ipsum dolor sit amet, consectetur adipiscing elit, sed do eiusmod tempor incididunt ut labore et dolore magna aliqua.</p><div class="card__rule"></div><p class="card__price">€ 10,50</p><p class="card__note">inkl. 19% MwSt. zzgl.<br><b>Versandkosten</b> &nbsp;|&nbsp; Lieferzeit 2 - 3 tage</p><a class="btn btn--steel">In den Warenkorb</a></article>
    <article class="card" style="left:15px;top:2140px"><div class="card__img" role="img" aria-label="Trockenfutter-Stücke"></div><h3 class="card__name">PRODUKTNAME GEHT HIER</h3><div class="card__dots"></div><p class="card__desc">Lorem ipsum dolor sit amet, consectetur adipiscing elit, sed do eiusmod tempor incididunt ut labore et dolore magna aliqua.</p><div class="card__rule"></div><p class="card__price">€ 10,50</p><p class="card__note">inkl. 19% MwSt. zzgl.<br><b>Versandkosten</b> &nbsp;|&nbsp; Lieferzeit 2 - 3 tage</p><a class="btn btn--steel">In den Warenkorb</a></article>
    <article class="card" style="left:146px;top:2140px"><div class="card__img" role="img" aria-label="Trockenfutter-Stücke"></div><h3 class="card__name">PRODUKTNAME GEHT HIER</h3><div class="card__dots"></div><p class="card__desc">Lorem ipsum dolor sit amet, consectetur adipiscing elit, sed do eiusmod tempor incididunt ut labore et dolore magna aliqua.</p><div class="card__rule"></div><p class="card__price">€ 10,50</p><p class="card__note">inkl. 19% MwSt. zzgl.<br><b>Versandkosten</b> &nbsp;|&nbsp; Lieferzeit 2 - 3 tage</p><a class="btn btn--steel">In den Warenkorb</a></article>
    <article class="card" style="left:276px;top:2140px"><div class="card__img" role="img" aria-label="Trockenfutter-Stücke"></div><h3 class="card__name">PRODUKTNAME GEHT HIER</h3><div class="card__dots"></div><p class="card__desc">Lorem ipsum dolor sit amet, consectetur adipiscing elit, sed do eiusmod tempor incididunt ut labore et dolore magna aliqua.</p><div class="card__rule"></div><p class="card__price">€ 10,50</p><p class="card__note">inkl. 19% MwSt. zzgl.<br><b>Versandkosten</b> &nbsp;|&nbsp; Lieferzeit 2 - 3 tage</p><a class="btn btn--steel">In den Warenkorb</a></article>

    <a class="btn btn--steel" style="left:135px;top:2362px;width:138px;height:19px;font-size:7px">Zum Online-Shop</a>
  </section>

  <section class="newsletter">
    <h2 class="newsletter__title">Newsletter anfordern und 5 Euro Gutschein sichern</h2>
    <p class="newsletter__sub">Angebote &amp; Neuigkeiten direkt per E-Mail! (Abmeldung jederzeit möglich)</p>
    <div class="newsletter__input">Email</div>
    <div class="newsletter__btn">JETZT ANMELDEN</div>
  </section>

  <footer class="footer">
    <div class="footer-brand">
      <div class="footer-brand__name">Pfotenküche</div>
      <div class="footer-brand__circle"></div>
    </div>
    <p class="address" style="top:2646px">Company Address will be here &nbsp;|&nbsp; 00112233 &nbsp;|&nbsp; Country Name will go here</p>
    <p class="address" style="top:2659px">Fon (0020) 123 44 567 &nbsp;·&nbsp; Fax (0020) 123 44 567</p>
    <p class="address" style="top:2672px"><a>www.pfotenkueche-natur.ch</a> &nbsp;|&nbsp; <a>hallo@pfotenkueche-natur.ch</a></p>
    <div class="socials" aria-label="Soziale Netzwerke"><span></span><span></span><span></span><span></span><span></span></div>

    <h2 class="contact__title script">Kontaktieren Sie uns jetzt</h2>
    <p class="contact__sub">Sie können uns wie folgt erreichen. Wir freuen uns über Ihre Kontakt Anfrage.</p>
    <div class="field field--active" style="left:15px;top:2786px;width:183px">Dein Name</div>
    <div class="field" style="left:212px;top:2786px;width:181px">Deine E-Mail</div>
    <div class="field" style="left:15px;top:2816px;width:378px">Fach</div>
    <div class="field" style="left:15px;top:2846px;width:378px">Deine Nachricht</div>
    <div class="field" style="left:15px;top:2878px;width:378px;height:6px"></div>
    <div class="copy-check">Kopie an sich selbst senden <i></i></div>
    <a class="btn btn--orange" style="left:288px;top:2924px;width:105px;height:19px;font-size:7px">Nachricht senden</a>

    <div class="bottom-bar">
      <span>© 2017 Pfotenküche - Alle Rechte vorbehalten</span>
      <nav>DATENSCHUTZ &nbsp;|&nbsp; IMPRESSUM &nbsp;|&nbsp; AGB &nbsp;|&nbsp; KONTAKT</nav>
    </div>
  </footer>

</main>
</body>
</html>
```